Coastline Premier Retreats Business Card Design

Design a business card for Coastline Premier Retreats. Look at the website for colors and reference. Card should have logo, name, title, office number, mobile number, email, URL and a tagline like, "Luxury Hotel & Resort Email Marketing" (This might change).

https://www.coastlinepremierretreats.example

The rest I will leave up to your imagination.

Contact Information for Business Card

Logo, name, title, office number, mobile number, email, URL and a tagline like, "Luxury Hotel & Resort Email Marketing" (This might change).

```html
<!DOCTYPE html>
<html lang="en">
<head>
<meta charset="utf-8">
<title>Coastline Premier Retreats – Business Card</title>
<link rel="stylesheet" href="https://fonts.googleapis.com/css2?family=Montserrat:wght@600;800&family=Open+Sans:wght@400;600&display=swap">
<style>
  :root {
    --orange: #f37321;
    --cream: #fffdf3;
    --ink: #111111;
    --white: #ffffff;
    --backdrop: #e2e3e5;
  }
  * { box-sizing: border-box; margin: 0; padding: 0; }
  html, body { width: 1200px; height: 780px; overflow: hidden; }
  body {
    background: var(--backdrop);
    font-family: "Open Sans", Arial, sans-serif;
    display: flex;
    align-items: center;
    justify-content: center;
    gap: 40px;
  }
  .card {
    position: relative;
    width: 540px;
    height: 310px;
    overflow: hidden;
  }
  /* Front */
  .card-front { background: var(--cream); }
  .brand {
    position: absolute;
    display: flex;
    align-items: center;
    gap: 10px;
    font-family: "Montserrat", Arial, sans-serif;
    font-weight: 800;
    text-transform: uppercase;
    line-height: 1.05;
  }
  .brand-mark { width: 14px; height: 14px; flex: none; }
  .card-front .brand {
    left: 200px; top: 52px;
    color: var(--ink);
    font-size: 21px;
    letter-spacing: 1px;
  }
  .card-front .brand-mark { background: var(--orange); }
  .person {
    position: absolute;
    left: 50px; top: 150px;
    text-align: right;
    font-family: "Montserrat", Arial, sans-serif;
  }
  .person-name { font-size: 25px; font-weight: 800; letter-spacing: 0.3px; }
  .person-first { color: var(--orange); }
  .person-last { color: var(--ink); }
  .person-title { font-size: 12px; font-weight: 600; color: var(--ink); letter-spacing: 1px; margin-top: 2px; }
  .divider {
    position: absolute;
    left: 278px; top: 140px;
    width: 1px; height: 82px;
    background: var(--ink);
  }
  .contacts {
    position: absolute;
    left: 292px; top: 140px;
    list-style: none;
    font-size: 10.5px;
    color: var(--ink);
    line-height: 20px;
  }
  .contacts li { display: flex; align-items: center; gap: 7px; white-space: nowrap; }
  .contacts svg { width: 11px; height: 11px; flex: none; }
  .tagline-band {
    position: absolute;
    left: 0; right: 0; top: 257px;
    height: 26px;
    background: var(--orange);
    color: var(--white);
    font-size: 12px;
    line-height: 26px;
    padding-left: 205px;
    letter-spacing: 0.3px;
  }
  /* Back */
  .card-back {
    background: var(--orange);
    display: flex;
    align-items: center;
    justify-content: center;
  }
  .card-back .brand {
    position: static;
    color: var(--white);
    font-size: 30px;
    letter-spacing: 2px;
    gap: 14px;
  }
  .card-back .brand-mark { background: var(--white); width: 20px; height: 20px; }
</style>
</head>
<body>
  <section class="card card-front" aria-label="Business card front">
    <div class="brand">
      <span class="brand-mark"></span>
      <span class="brand-name">Coastline Premier<br>Retreats</span>
    </div>

    <div class="person">
      <p class="person-name"><span class="person-first">Marta</span> <span class="person-last">Lindqvist</span></p>
      <p class="person-title">Co-Founder</p>
    </div>

    <div class="divider"></div>

    <ul class="contacts">
      <li>
        <svg viewBox="0 0 12 12" aria-hidden="true"><path d="M2.5 1 L4.5 1 L5.2 3.4 L4 4.3 Q5 6.8 7.7 8 L8.6 6.8 L11 7.5 L11 9.5 Q10.5 11 9 11 Q1 10 1 2.5 Q1 1 2.5 1 Z" fill="var(--orange)"/></svg>
        (555) 214-3087
      </li>
      <li>
        <svg viewBox="0 0 12 12" aria-hidden="true"><rect x="3" y="0.7" width="6" height="10.6" rx="1" fill="none" stroke="var(--orange)" stroke-width="1.2"/><circle cx="6" cy="9.4" r="0.7" fill="var(--orange)"/></svg>
        (555) 402-6618
      </li>
      <li>
        <svg viewBox="0 0 12 12" aria-hidden="true"><circle cx="6" cy="6" r="5" fill="none" stroke="var(--orange)" stroke-width="1.2"/><ellipse cx="6" cy="6" rx="2.2" ry="5" fill="none" stroke="var(--orange)" stroke-width="1"/><path d="M1 6 H11" stroke="var(--orange)" stroke-width="1"/></svg>
        www.coastlinepremierretreats.example
      </li>
      <li>
        <svg viewBox="0 0 12 12" aria-hidden="true"><rect x="0.8" y="2.5" width="10.4" height="7.5" fill="var(--orange)"/><path d="M0.8 2.5 L6 6.8 L11.2 2.5" fill="none" stroke="var(--white)" stroke-width="1"/></svg>
        info@coastlinepremierretreats.example
      </li>
    </ul>

    <p class="tagline-band">Luxury Hotel &amp; Resort Email Marketing</p>
  </section>

  <section class="card card-back" aria-label="Business card back">
    <div class="brand">
      <span class="brand-mark"></span>
      <span class="brand-name">Coastline Premier<br>Retreats</span>
    </div>
  </section>
</body>
</html>
```